Tolvane Inc., a third party debt collection agency needs a Website

Tolvane needs a very basic website (3 basic pages) so that consumers can download forms, potential employees can get required EEO language and see potential jobs, and to show that they are a consumer friendly organization.

I've attached a list of requirements and wishes titled "Tolvane Website Specifications"

Target Market(s)

Consumers that need to repay their government loans; Tolvane will walk through the process to assist them.

Industry/Entity Type

Financial Service

Coding

Coded - Design and coding required

Number of Pages Required

1 page

Font styles to use
Sans Serif

Colors
0355a3

Requirements
Must have
• Tolvane Logo
• See document "Tolvane Website Specifications" for all requirements

```html
<!DOCTYPE html>
<html lang="en">
<head>
<meta charset="utf-8">
<title>Tolvane, Inc.</title>
<link rel="stylesheet" href="https://fonts.googleapis.com/css2?family=Open+Sans:wght@400;600;700&family=Ubuntu:wght@500;700&display=swap">
<style>
:root{
  --navy:#1f1a62;
  --navy-deep:#18144f;
  --maroon:#7a1320;
  --ink:#2b2b2b;
  --muted:#444;
  --band:#f7f7f7;
  --rule:#dedede;
  --caption:#3b3d40;
}
*{margin:0;padding:0;box-sizing:border-box}
html,body{width:919px;height:1200px;overflow:hidden;background:#fff}
body{position:relative;font-family:"Open Sans",sans-serif;color:var(--ink)}
.abs{position:absolute}
.top-rule{left:0;top:0;width:919px;height:2px;background:var(--navy)}
.brand{font-family:"Ubuntu",sans-serif;font-weight:700;letter-spacing:-.3px}
.site-brand{left:122px;top:48px;font-size:26px;color:var(--maroon);line-height:1}
.contact-line{top:20px;font-size:10px;color:#444;display:flex;align-items:center;gap:8px}
.icon-ring{width:20px;height:20px;border:1.5px solid var(--maroon);border-radius:50%;display:flex;align-items:center;justify-content:center}
.main-nav{top:64px;left:0;font-size:10px;font-weight:600;color:#333;letter-spacing:.1px}
.main-nav span{position:absolute;top:0;white-space:nowrap}
.main-nav .current{color:var(--navy)}
.search-btn{left:766px;top:57px;width:28px;height:28px;border-radius:50%;background:var(--navy)}
.hero{left:0;top:95px;width:919px;height:395px}
.caption-title{left:588px;top:238px;width:331px;height:37px;background:rgba(50,52,56,.88);clip-path:polygon(0 0,100% 0,100% 100%,12px 100%);color:#fff;font-weight:700;font-size:14px;padding:10px 0 0 24px}
.caption-text{left:430px;top:279px;width:489px;height:43px;background:rgba(90,94,100,.75);clip-path:polygon(8px 0,100% 0,100% 100%,0 100%);color:#fff;font-size:8.6px;line-height:12px;padding:9px 0 0 24px}
h1{left:0;width:919px;top:494px;text-align:center;font-family:"Ubuntu",sans-serif;font-weight:700;font-size:24px;color:var(--navy)}
.accent{color:var(--maroon)}
.intro{left:136px;width:647px;top:532px;text-align:center;font-size:7.9px;line-height:15px;color:var(--ink);letter-spacing:-.05px}
.read-more{height:24px;width:86px;display:flex;background:var(--maroon);color:#fff;font-size:8.2px;font-weight:600;align-items:center}
.read-more b{flex:1;padding-left:10px;font-weight:600}
.read-more i{width:22px;height:24px;background:var(--navy);display:flex;align-items:center;justify-content:center}
.divider{left:123px;top:648px;width:672px;height:1px;background:var(--rule)}
h2{top:667px;font-family:"Ubuntu",sans-serif;font-weight:700;font-size:18px;color:var(--navy)}
.thumb{width:153px;height:127px;border:1px solid #ccc;padding:3px;background:#fff;box-shadow:0 1px 2px rgba(0,0,0,.15)}
.thumb div{width:100%;height:100%}
.blurb{width:162px;top:704px;font-size:7.8px;line-height:14.4px;color:#444;text-align:justify;letter-spacing:-.05px}
.partners{left:0;top:866px;width:919px;height:152px;background:var(--band);border-top:1px solid #e4e4e4}
.partners .split{left:459px;top:0;width:1px;height:152px;background:#d8d8d8}
.partner-title{top:34px;width:459px;text-align:center;font-size:12px;font-weight:600;color:var(--navy)}
.footer{left:0;top:1018px;width:919px;height:140px;background:var(--navy)}
.footer .sep{top:30px;width:1px;height:92px;background:rgba(255,255,255,.12)}
.footer-brand{left:123px;top:74px;font-size:24px;color:#fff}
.footer h3{top:28px;font-size:11.5px;font-weight:600;color:#fff}
.footer ul{list-style:none;font-size:8.8px;color:#fff;line-height:16.8px}
.footer li{display:flex;align-items:flex-start;gap:7px}
.footer li svg{margin-top:4px;flex:none}
.legal{left:0;top:1158px;width:919px;height:42px;background:var(--maroon);color:#fff;font-size:8px;text-align:center;padding-top:14px}
</style>
</head>
<body>
<div class="abs top-rule"></div>

<header>
  <div class="abs brand site-brand">Tolvane, Inc.</div>
  <div class="abs contact-line" style="left:520px">
    <span class="icon-ring"><svg width="9" height="7" viewBox="0 0 9 7"><rect width="9" height="7" rx="1" fill="#7a1320"/><path d="M0 0l4.5 3.5L9 0" stroke="#fff" stroke-width=".9" fill="none"/></svg></span>
    Email: info@company.Com
  </div>
  <div class="abs contact-line" style="left:677px">
    <span class="icon-ring"><svg width="9" height="9" viewBox="0 0 10 10"><path d="M2 1l2 2-1 1.3c.6 1.2 1.5 2.1 2.7 2.7L7 6l2 2-1.3 1.5C4.5 9.2.8 5.5.5 2.3z" fill="#7a1320"/></svg></span>
    Phone: 000-000-0009
  </div>
  <nav class="abs main-nav">
    <span class="current" style="left:333px">HOME
      <svg style="position:absolute;left:-2px;top:14px" width="34" height="6" viewBox="0 0 34 6"><path d="M1 2c8 5 20 5 32 0" stroke="#1f1a62" stroke-width="2" fill="none"/></svg>
    </span>
    <span style="left:398px">CONSUMER INFORMATION</span>
    <span style="left:559px">CAREERS @ TOLVANE</span>
    <span style="left:699px">CONTACT</span>
  </nav>
  <div class="abs search-btn">
    <svg width="28" height="28" viewBox="0 0 28 28"><circle cx="13" cy="13" r="3.3" stroke="#fff" stroke-width="1.6" fill="none"/><path d="M15.5 15.5l2.5 2.5" stroke="#fff" stroke-width="1.8"/></svg>
  </div>
</header>

<section class="abs hero">
  <svg width="919" height="395" viewBox="0 0 919 395" role="img" aria-label="Photo of smiling call centre agents wearing headsets at their desks">
    <defs>
      <linearGradient id="heroTone" x1="0" y1="0" x2="1" y2="1">
        <stop offset="0" stop-color="#b8c2cc"/>
        <stop offset=".45" stop-color="#8b96a3"/>
        <stop offset="1" stop-color="#c9d2da"/>
      </linearGradient>
    </defs>
    <rect width="919" height="395" fill="url(#heroTone)"/>
    <path d="M0 337C90 375 190 392 290 380C440 362 560 322 700 320C790 319 860 322 919 335V395H0Z" fill="#fff"/>
    <path d="M0 337C90 375 190 392 290 380C440 362 560 322 700 320C790 319 860 322 919 335" stroke="#1f1a62" stroke-width="3" fill="none"/>
    <path d="M50 155L34 175L50 195" stroke="#fff" stroke-width="1.2" fill="none"/>
    <path d="M870 172L884 185" stroke="rgba(255,255,255,.6)" stroke-width="1.2"/>
    <rect x="815" y="267" width="24" height="2" fill="#7a1320"/>
    <rect x="827" y="272" width="12" height="2" fill="#fff"/>
    <rect x="827" y="278" width="12" height="2" fill="#fff"/>
    <rect x="827" y="284" width="12" height="2" fill="#fff"/>
  </svg>
</section>
<div class="abs caption-title">WELCOME TO TOLVANE</div>
<div class="abs caption-text">Lorem ipsum dolor sit amet, consectetur adipiscing elit, sed do eiusmod tempornc<br>ididunt ut labore et dolore magna aliqua. Ut enim ad minim veniam.</div>

<main>
  <h1 class="abs">Welcome to <span class="accent">Tolvane</span></h1>
  <p class="abs intro">Tolvane is a third party debt collection agency that is focused on the collection of higher education loans.&nbsp; Tolvane is compliant with all federal, state, and local laws and is committed to the professional and fair treatment of consumers.&nbsp; Our goal is to assist consumers in resolving their obligations in the manner that best meets their needs and to provide information necessary in order for consumers to make an informed decision. Sed ut perspiciatis unde omnis iste natus error sit voluptatem accusantium doloremque lauda ntim, totam rem aperiam, eaque ipsa quae ab illo invenue lauda ntim, totam rem aperitore veritatis et quasi archi.</p>
  <a class="abs read-more" style="left:417px;top:601px"><b>READ MORE</b><i><svg width="8" height="8" viewBox="0 0 8 8"><circle cx="4" cy="4" r="4" fill="#fff"/><path d="M3.2 2.3L5 4 3.2 5.7" stroke="#1f1a62" stroke-width="1.2" fill="none"/></svg></i></a>
  <div class="abs divider"></div>

  <h2 class="abs" style="left:123px">Consumer <span class="accent">Information</span></h2>
  <div class="abs thumb" style="left:124px;top:702px"><div role="img" aria-label="Photo of customer service agents with headsets working at computers" style="background:linear-gradient(135deg,#9aa6b4,#5f6c7c 55%,#c0c8d0)"></div></div>
  <p class="abs blurb" style="left:290px">Sed ut perspiciatis unde omnis iste natus error sit voluptatem accusantium dolo-remque laudantium, totam rem aperiam, ea que ipsa quae ab illo inventore veritatis et quasi architectobea tae vitae dicta sunt explicaboemo enim ipsam volupta</p>
  <a class="abs read-more" style="left:290px;top:800px"><b>READ MORE</b><i><svg width="8" height="8" viewBox="0 0 8 8"><circle cx="4" cy="4" r="4" fill="#fff"/><path d="M3.2 2.3L5 4 3.2 5.7" stroke="#1f1a62" stroke-width="1.2" fill="none"/></svg></i></a>

  <h2 class="abs" style="left:468px">Careers <span class="accent">@ Tolvane</span></h2>
  <div class="abs thumb" style="left:469px;top:702px"><div role="img" aria-label="Photo of a smiling team of young professionals standing together" style="background:linear-gradient(135deg,#c9b7a6,#8d7a6c 50%,#aab4c2)"></div></div>
  <p class="abs blurb" style="left:635px">Sed ut perspiciatis unde omnis iste natus error sit voluptatem accusantium dolo-remque laudantium, totam rem aperiam, ea que ipsa quae ab illo inventore veritatis et quasi architectobea tae vitae dicta sunt explicaboemo enim ipsam volupta</p>
  <a class="abs read-more" style="left:635px;top:800px"><b>READ MORE</b><i><svg width="8" height="8" viewBox="0 0 8 8"><circle cx="4" cy="4" r="4" fill="#fff"/><path d="M3.2 2.3L5 4 3.2 5.7" stroke="#1f1a62" stroke-width="1.2" fill="none"/></svg></i></a>
</main>

<section class="abs partners">
  <div class="abs split"></div>
  <p class="abs partner-title" style="left:20px">Tolvane is accredited the Fair Commerce Council</p>
  <div class="abs" style="left:222px;top:74px;width:91px;height:35px;border-radius:5px;background:#1d4d6b" aria-label="Accreditation badge"></div>
  <p class="abs partner-title" style="left:459px">Tolvane is a member of Collectors Guild International</p>
  <div class="abs" style="left:586px;top:72px;width:106px;height:45px;background:#e6edf5" aria-label="Membership badge"></div>
</section>

<footer class="abs footer">
  <div class="abs brand footer-brand">Tolvane, Inc.</div>
  <div class="abs sep" style="left:334px"></div>
  <div class="abs sep" style="left:582px"></div>
  <h3 class="abs" style="left:405px">NAVIGATION</h3>
  <ul class="abs" style="left:406px;top:52px">
    <li>Home</li><li>Consumer Information</li><li>Careers @ Tolvane</li><li>Contact</li>
  </ul>
  <h3 class="abs" style="left:656px">CONTACT US</h3>
  <ul class="abs" style="left:657px;top:52px;line-height:15.5px">
    <li><svg width="6" height="8" viewBox="0 0 6 8"><path d="M3 8L.6 4A2.6 2.6 0 1 1 5.4 4Z" fill="#fff"/><circle cx="3" cy="2.7" r="1" fill="#1f1a62"/></svg><span>201 lorem ipsum dolor site,<br>tolvane dummy text,5482</span></li>
    <li><svg width="7" height="7" viewBox="0 0 10 10"><path d="M2 1l2 2-1 1.3c.6 1.2 1.5 2.1 2.7 2.7L7 6l2 2-1.3 1.5C4.5 9.2.8 5.5.5 2.3z" fill="#fff"/></svg><span>Phone:&nbsp; 555-014-2290</span></li>
    <li><svg width="7" height="6" viewBox="0 0 9 7"><rect width="9" height="7" rx="1" fill="#fff"/><path d="M0 0l4.5 3.5L9 0" stroke="#1f1a62" stroke-width=".9" fill="none"/></svg><span>info@tolvane.com</span></li>
  </ul>
</footer>
<div class="abs legal">© 2016 Tolvane. All copyrights are reserved&nbsp; Term of Use, Privay Policy</div>
</body>
</html>
```